Healthtech Wearable Device Product Packaging Design

We need a new product packaging design for SEA market with an international look to it.
Attached is our current China/Taiwan for your reference.
Our company name: Talvonmede means guiding light and provide care on 3 levels: Government community care, corporate health management, and family care.
Our company color schem is orange and white.

Target Market(s)

Health tech, Southeast Asia, International look
The final design should communicate "bringing healthcare closer you", a touch of friendliness, love and tender care. It does not give off just another wearable watch vibe.

Requirements
Must have
• Color scheme: Orange and white
Simple yet professional looking
Health tech but think out of the box
Distribution to B2B channel
Nice to have
• Eye catchy, trendy, support sustainability in one way or another
Should not have
• overcrowding feel, boring

```html
<!DOCTYPE html>
<html lang="en">
<head>
<meta charset="utf-8">
<title>Talvonmede TM 500S – Packaging Front Panel</title>
<link href="https://fonts.googleapis.com/css2?family=Open+Sans:wght@300;400;600&display=swap" rel="stylesheet">
<style>
  :root {
    --backdrop: #d6c3ad;
    --panel-white: #ffffff;
    --panel-fade: #ececec;
    --ink: #3e3a3b;
    --ink-soft: #4a4647;
    --badge: #2f2b2c;
    --orange: #e5844f;
    --orange-light: #ec9a6e;
    --pink: #e79aaa;
    --device: #3b3b3d;
    --device-dark: #26262a;
  }
  * { box-sizing: border-box; margin: 0; padding: 0; }
  html, body {
    width: 1200px;
    height: 840px;
    overflow: hidden;
    background: var(--backdrop);
    font-family: "Open Sans", sans-serif;
  }
  .stage {
    width: 1200px;
    height: 840px;
    display: flex;
    align-items: center;
    justify-content: center;
  }
  .front-panel {
    position: relative;
    width: 570px;
    height: 760px;
    background: linear-gradient(170deg, var(--panel-white) 0%, var(--panel-fade) 100%);
    overflow: hidden;
  }
  .colour-wedge {
    position: absolute;
    inset: 0;
    width: 100%;
    height: 100%;
  }
  .brand {
    position: absolute;
    left: 62px;
    top: 118px;
    display: flex;
    align-items: center;
    gap: 14px;
  }
  .brand-name {
    font-weight: 300;
    font-size: 68px;
    letter-spacing: 0.5px;
    color: var(--ink);
    line-height: 1;
  }
  .brand-dot {
    width: 22px;
    height: 22px;
    border-radius: 50%;
    background: var(--orange-light);
    margin-top: 14px;
  }
  .tagline {
    position: absolute;
    left: 66px;
    top: 220px;
    font-weight: 400;
    font-size: 22px;
    color: var(--ink-soft);
  }
  .model-badge {
    position: absolute;
    left: 62px;
    top: 330px;
    padding: 10px 20px;
    background: var(--badge);
    border-radius: 7px;
    color: #ffffff;
    font-weight: 400;
    font-size: 36px;
    line-height: 1.2;
  }
  .device-visual {
    position: absolute;
    left: 290px;
    top: 290px;
    width: 230px;
    height: 330px;
    border-radius: 40px 110px 110px 40px;
    background: radial-gradient(ellipse at 30% 45%, var(--device) 0%, var(--device-dark) 75%);
  }
  .compliance {
    position: absolute;
    right: 40px;
    bottom: 46px;
    display: flex;
    align-items: center;
    gap: 16px;
    color: #ffffff;
  }
  .compliance-text {
    font-size: 9px;
    font-weight: 400;
  }
  .compliance-mark {
    width: 14px;
    height: 10px;
    border: 1px solid #ffffff;
  }
</style>
</head>
<body>
  <main class="stage">
    <section class="front-panel">
      <svg class="colour-wedge" viewBox="0 0 570 760" preserveAspectRatio="none" aria-hidden="true">
        <defs>
          <linearGradient id="wedgeGradient" x1="0" y1="1" x2="1" y2="0">
            <stop offset="0%" stop-color="#e5844f"/>
            <stop offset="55%" stop-color="#e79aaa"/>
            <stop offset="100%" stop-color="#ec9a6e"/>
          </linearGradient>
        </defs>
        <polygon points="0,760 570,330 570,760" fill="url(#wedgeGradient)"/>
      </svg>

      <div class="brand">
        <span class="brand-name">Talvonmede</span>
        <span class="brand-dot"></span>
      </div>
      <p class="tagline">Bringing Healthcare Closer to You</p>

      <div class="model-badge">TM 500S</div>

      <div class="device-visual" role="img" aria-label="Product photo of the dark grey fitness band with its screen showing a blood oxygen reading of 98 percent"></div>

      <div class="compliance">
        <span class="compliance-text">Complies with NCRA Standards RF204417</span>
        <span class="compliance-mark"></span>
      </div>
    </section>
  </main>
</body>
</html>
```